Business Card Design

I already have a company logo for my company. I have a logo for the manufacturer we represent. I want a professional business card design.

```html
<!DOCTYPE html>
<html lang="en">
<head>
<meta charset="utf-8">
<title>Beacon Shield LLC – Business Card</title>
<link rel="stylesheet" href="https://fonts.googleapis.com/css2?family=Open+Sans:wght@400;600;700;800&display=swap">
<style>
  :root {
    --stage: #202022;
    --card: #1d1d21;
    --card-edge: #2a2a2f;
    --gold: #b98f2a;
    --red: #e31c25;
    --white: #ffffff;
    --soft-white: #e9e9ea;
    --pattern-a: #26262b;
    --pattern-b: #1b1b1f;
  }
  * { box-sizing: border-box; margin: 0; padding: 0; }
  html, body {
    width: 1200px; height: 780px; overflow: hidden;
    background: var(--stage);
    font-family: "Open Sans", Arial, sans-serif;
  }
  .stage {
    position: relative; width: 1200px; height: 780px;
  }
  .card {
    position: absolute; top: 235px;
    width: 540px; height: 309px;
    background: var(--card);
    border: 1px solid var(--card-edge);
    overflow: hidden;
  }
  .card--front { left: 30px; }
  .card--back { left: 630px; }

  /* brand name stand-in */
  .brand {
    position: absolute; display: flex; align-items: center; gap: 10px;
    color: var(--red); font-weight: 800; text-transform: uppercase;
    letter-spacing: 1px; white-space: nowrap;
  }
  .brand__dot {
    width: 22px; height: 22px; border-radius: 50%;
    background: var(--gold); flex: none;
  }
  .card--front .brand { top: 62px; left: 210px; font-size: 22px; }

  .info-band {
    position: absolute; left: 0; top: 148px; width: 470px; height: 92px;
    display: flex;
  }
  .info-band__name {
    width: 215px; background: var(--gold);
    padding: 20px 0 0 22px;
  }
  .person-name { font-size: 21px; font-weight: 700; color: var(--white); line-height: 1.1; }
  .person-name__first { color: var(--red); }
  .person-role { font-size: 13px; color: var(--white); margin-top: 5px; }

  .info-band__junction {
    width: 40px;
    background: linear-gradient(90deg, var(--gold) 0 50%, var(--red) 50% 100%);
    display: flex; align-items: center; justify-content: center;
  }
  .junction-mark {
    width: 34px; height: 34px; border-radius: 50%;
    background: var(--card); border: 2px solid var(--soft-white);
  }

  .info-band__contact {
    flex: 1; background: var(--red);
    padding: 10px 0 0 22px;
    display: flex; flex-direction: column; gap: 3px;
  }
  .contact-line {
    display: flex; align-items: center; gap: 8px;
    color: var(--white); font-size: 14px; line-height: 21px;
  }
  .contact-line svg { width: 14px; height: 14px; flex: none; }

  .address {
    position: absolute; left: 22px; top: 262px;
    color: var(--soft-white); font-size: 13.5px; letter-spacing: .2px;
  }

  .pattern-field {
    position: absolute; inset: 0;
    background: radial-gradient(ellipse at 70% 60%, var(--pattern-a), var(--pattern-b) 75%);
  }
  .card--back .brand {
    top: 50%; left: 50%; transform: translate(-50%, -50%);
    font-size: 30px;
  }
  .card--back .brand__dot { width: 30px; height: 30px; }
</style>
</head>
<body>
<main class="stage">

  <section class="card card--front" aria-label="Business card front">
    <div class="brand"><span class="brand__dot"></span>Beacon Shield LLC</div>

    <div class="info-band">
      <div class="info-band__name">
        <p class="person-name"><span class="person-name__first">Marta</span> Kovalin</p>
        <p class="person-role">Managing Director</p>
      </div>
      <div class="info-band__junction"><span class="junction-mark"></span></div>
      <div class="info-band__contact">
        <p class="contact-line">
          <svg viewBox="0 0 16 16" aria-hidden="true"><path fill="#fff" d="M3.6 1.5l2.3 2.6-1.3 1.8c.9 2 2.5 3.6 4.5 4.5l1.8-1.3 2.6 2.3-1.4 2.4C7 13.6 2.4 9 2.2 3z"/></svg>
          (555) 014-2290
        </p>
        <p class="contact-line">
          <svg viewBox="0 0 16 16" aria-hidden="true"><rect x="1.5" y="3.5" width="13" height="9" rx="1" fill="none" stroke="#fff" stroke-width="1.5"/><path d="M2 4.5l6 4.5 6-4.5" fill="none" stroke="#fff" stroke-width="1.5"/></svg>
          info@beaconshield.co
        </p>
        <p class="contact-line">
          <svg viewBox="0 0 16 16" aria-hidden="true"><circle cx="8" cy="8" r="6.3" fill="none" stroke="#fff" stroke-width="1.4"/><ellipse cx="8" cy="8" rx="2.8" ry="6.3" fill="none" stroke="#fff" stroke-width="1.2"/><path d="M1.8 8h12.4" stroke="#fff" stroke-width="1.2"/></svg>
          www.beaconshield.co
        </p>
      </div>
    </div>

    <p class="address">4217 Harlow Ct #204, Palm Bay, FL 32905, USA</p>
  </section>

  <section class="card card--back" aria-label="Business card back">
    <div class="pattern-field" role="img" aria-label="Dark repeating brand pattern backdrop"></div>
    <div class="brand"><span class="brand__dot"></span>Beacon Shield LLC</div>
  </section>

</main>
</body>
</html>
```